New career and executive coaching business needs a business card design including logo

Company name: 'Bramblefield Growth Partners.' The aim of my coaching engagements is to help people improve their communication in the workplace and achieve their career goals. The process involves working with individuals to help them uncover their strengths and talents, then leverage those to improve their working lives. The Tarwick Inventory is the starting point to the process. I am after an exciting and interesting business card design (including logo)which is professional yet will still get people's attention.

Industry/Entity Type

Business

Contact Information for Business Card

Name: Malcolm Dervaney
Position: Owner
Address: 58 Quorrin Ct, Elmbridge Vic 3190
Phone: 0418923047
Website: bramblefieldgrowth.com.au
Email: malcolm@bgp.com.au

Colors
33a6d7
00a990
0355a3
3176b5

Requirements
Must have
• logo

```html
<!DOCTYPE html>
<html lang="en">
<head>
<meta charset="utf-8">
<title>Bramblefield Growth Partners – Business Cards</title>
<link href="https://fonts.googleapis.com/css2?family=PT+Sans:wght@400;700&display=swap" rel="stylesheet">
<style>
  :root {
    --sky: #33a6d7;
    --teal: #00a990;
    --navy: #0355a3;
    --mid-blue: #3176b5;
    --ring-grey: #a7a9ac;
    --card: #ffffff;
    --backdrop: #ebe8e5;
  }
  * { margin: 0; padding: 0; box-sizing: border-box; }
  html, body {
    width: 1200px; height: 900px; overflow: hidden;
    background: var(--backdrop);
    font-family: "PT Sans", "Myriad Pro", Arial, sans-serif;
  }
  .canvas { position: relative; width: 1200px; height: 900px; }
  .card {
    position: absolute;
    background: var(--card);
    box-shadow: 0 6px 18px rgba(0,0,0,0.12);
  }
  .card--front { left: 238px; top: 62px; width: 555px; height: 342px; }
  .card--back  { left: 457px; top: 518px; width: 560px; height: 342px; }

  .contact { position: absolute; left: 34px; top: 86px; color: var(--navy); }
  .contact__name { font-size: 19px; font-weight: 700; color: var(--teal); line-height: 1.1; }
  .contact__role { font-size: 15px; line-height: 1.2; }
  .contact__address { margin-top: 16px; font-size: 15px; line-height: 20px; }
  .contact__list { margin-top: 14px; list-style: none; font-size: 15px; line-height: 20px; }
  .contact__list li { display: flex; align-items: center; gap: 8px; }
  .contact__list svg { width: 11px; height: 11px; flex: none; }

  .brand { position: absolute; display: flex; align-items: center; }
  .brand__dot {
    flex: none; border-radius: 50%;
    background: var(--mid-blue);
    border: 4px solid var(--ring-grey);
  }
  .brand__name {
    color: var(--navy); font-weight: 700; text-transform: uppercase;
  }
  .brand--front {
    left: 318px; top: 80px; width: 200px;
    flex-direction: column; gap: 14px; text-align: center;
  }
  .brand--front .brand__dot { width: 110px; height: 110px; }
  .brand--front .brand__name { font-size: 20px; line-height: 1.15; }

  .brand--back { left: 114px; top: 119px; gap: 22px; }
  .brand--back .brand__dot { width: 104px; height: 104px; }
  .brand--back .brand__name { font-size: 30px; line-height: 1.1; }
</style>
</head>
<body>
<main class="canvas">
  <section class="card card--front">
    <div class="contact">
      <p class="contact__name">Malcolm Dervaney</p>
      <p class="contact__role">Owner</p>
      <p class="contact__address">58 Quorrin Ct, Elmbridge<br>Vic 3190</p>
      <ul class="contact__list">
        <li>
          <svg viewBox="0 0 12 12" aria-hidden="true"><path fill="var(--teal)" d="M2.5 0.5l2 2.5-1.2 1.3c.7 1.6 2 2.9 3.5 3.6L8 6.6l2.6 2-1.1 2.6C5 11.2.8 7 .5 2.6z"/></svg>
          <span>0418923047</span>
        </li>
        <li>
          <svg viewBox="0 0 12 12" aria-hidden="true"><rect x="0.5" y="2" width="11" height="8" fill="var(--teal)"/><path d="M0.8 2.4L6 6.6l5.2-4.2" fill="none" stroke="#fff" stroke-width="1"/></svg>
          <span>malcolm@bgp.com.au</span>
        </li>
        <li>
          <svg viewBox="0 0 12 12" aria-hidden="true"><circle cx="6" cy="6" r="5.5" fill="var(--teal)"/><path d="M3 4.5c1.5-.8 2.5.5 2 1.8S3.8 8.5 4.5 10M7.5 2c-.5 1.4.8 2 2 2.2" fill="none" stroke="#fff" stroke-width="1"/></svg>
          <span>bramblefieldgrowth.com.au</span>
        </li>
      </ul>
    </div>
    <div class="brand brand--front">
      <span class="brand__dot" aria-hidden="true"></span>
      <p class="brand__name">Bramblefield<br>Growth Partners</p>
    </div>
  </section>

  <section class="card card--back">
    <div class="brand brand--back">
      <span class="brand__dot" aria-hidden="true"></span>
      <p class="brand__name">Bramblefield<br>Growth Partners</p>
    </div>
  </section>
</main>
</body>
</html>
```